Website redesign www.marigoldlawpc.com law firm site

Need to redesign the website that I currently have to look more modern and professional. Would also like to be able to make updates and post without having a huge hassle. See current www.marigoldlawpc.com. I just think that it looks very immature and it's very templated there's no ability for me to make posts or Add links or anything like that

Target Market(s)

California people looking for a powerhouse attorney in

Industry/Entity Type

Legal

Number of Pages Required

3 page

Font styles to use
Serif
Sans Serif

Colors
ec1f27
000000
ffffff

Requirements
Must have
• Must be mobile friendly. Must look professional and have ability to post links to other websites. Must have ability to post blogs or articles. Would like to be able to read my FeeTrove account and also have the ability to upload forms for people to download
Nice to have
• Simple design easy to use and not cluttered with too much text

```html
<!DOCTYPE html>
<html lang="en">
<head>
<meta charset="utf-8">
<title>Marigold Law, P.C.</title>
<link href="https://fonts.googleapis.com/css2?family=Lora:ital,wght@0,400;0,700;1,400&family=Open+Sans:wght@400;600;700&display=swap" rel="stylesheet">
<style>
:root{
  --red:#ec1f27;
  --red-dark:#c8161d;
  --black:#000000;
  --ink:#1c1c1c;
  --text:#555555;
  --white:#ffffff;
  --grey-bg:#f1f1f1;
  --footer:#1e1e1e;
  --footer-line:#3a3a3a;
  --serif:'Lora', Georgia, serif;
  --sans:'Open Sans', Arial, sans-serif;
}
*{box-sizing:border-box;margin:0;padding:0}
html,body{width:1200px;height:2469px;overflow:hidden;background:var(--white)}
body{position:relative;font-family:var(--sans);color:var(--text)}
a{text-decoration:none;color:inherit}
.abs{position:absolute}

/* header */
.topline{position:absolute;left:0;top:0;width:1200px;height:4px;background:var(--red)}
.brand{position:absolute;left:74px;top:14px;width:256px;text-align:center;font-family:var(--serif);color:var(--red);font-weight:400}
.brand .name{font-size:38px;line-height:44px;letter-spacing:.5px}
.brand .pc{display:flex;align-items:center;gap:10px;font-size:16px;line-height:18px}
.brand .pc::before,.brand .pc::after{content:"";flex:1;height:2px;background:var(--red)}
.social-top{position:absolute;left:572px;top:16px;display:flex;gap:6px}
.dot{width:29px;height:29px;border-radius:50%}
.dot.blue{background:#3b5998}.dot.sky{background:#2fa7e0}.dot.teal{background:#27a1d4}
.contact-top{position:absolute;top:16px;display:flex;align-items:center;gap:10px;font-family:var(--serif);font-size:15px;color:var(--ink)}
.ring{width:29px;height:29px;border-radius:50%;border:2px solid var(--red);display:flex;align-items:center;justify-content:center}
.nav{position:absolute;right:97px;top:58px;display:flex;gap:26px;font-family:var(--serif);font-weight:700;font-size:15px;color:var(--ink)}
.nav .active{color:var(--red)}

/* hero */
.hero{position:absolute;left:0;top:86px;width:1200px;height:429px;background:linear-gradient(180deg,#9fb1c4 0%,#7a8797 45%,#5b5f66 100%)}
.hero h1{position:absolute;top:130px;width:100%;text-align:center;font-family:var(--serif);font-weight:700;font-size:60px;color:var(--white)}
.hero p{position:absolute;top:203px;width:100%;text-align:center;font-size:21px;color:var(--white)}
.btn-red{position:absolute;left:501px;top:249px;width:196px;height:38px;background:var(--red);color:var(--white);font-weight:700;font-size:15px;display:flex;align-items:center;justify-content:center}
.slider-dots{position:absolute;top:384px;left:532px;display:flex;gap:8px}
.slider-dots span{width:30px;height:4px;background:rgba(255,255,255,.85)}
.slider-dots span:first-child{background:var(--red)}

/* welcome */
.welcome h2{position:absolute;left:99px;top:566px;font-family:var(--serif);font-size:24px;font-weight:400;color:var(--black);letter-spacing:.3px}
.welcome p{position:absolute;left:99px;width:548px;font-size:13px;line-height:23px}
.read-more{position:absolute;font-size:13px;font-weight:700;color:var(--red)}
.wordcloud{position:absolute;left:690px;top:540px;width:420px;height:300px;background:linear-gradient(135deg,#e7d3c4,#b86a4f 55%,#6e1e14);opacity:.85}

/* practice band */
.band{position:absolute;left:0;top:887px;width:1200px;height:284px;background:linear-gradient(90deg,#e8363c,#d8232a 50%,#e4333a)}
.band .v{position:absolute;width:2px;background:rgba(255,255,255,.9)}
.band .pin{position:absolute;width:12px;height:12px;border-radius:50%;background:var(--white)}
.area{position:absolute;width:160px;text-align:center;color:var(--white);font-family:var(--serif);font-weight:700;font-size:16px}
.area svg{display:block;margin:0 auto 6px}

/* blog */
.blog-title{position:absolute;top:1218px;width:100%;text-align:center;font-family:var(--serif);font-size:24px;color:var(--black)}
.card{position:absolute;top:1277px;width:317px}
.card .photo{height:203px}
.card h3{margin-top:20px;font-family:var(--serif);font-weight:700;font-size:17px;color:var(--ink)}
.card .meta{margin-top:10px;font-size:12px;color:var(--red);display:flex;gap:8px;align-items:center}
.card .meta i{font-style:normal;color:#bbb}
.card p{margin-top:10px;font-size:12.5px;line-height:22px}
.card .more{display:block;margin-top:14px;font-size:13px;font-weight:700;color:var(--red)}
.arrow-btn{position:absolute;top:1360px;width:40px;height:40px;border-radius:50%;background:#ececec;display:flex;align-items:center;justify-content:center}

/* testimonial */
.testimonial{position:absolute;left:0;top:1695px;width:1200px;height:214px;background:var(--grey-bg)}
.quote-bg{position:absolute;left:104px;top:40px;width:110px;height:110px;border-radius:50%;background:#e1e1e1}
.avatar{position:absolute;left:178px;top:42px;width:104px;height:104px;border-radius:50%;background:linear-gradient(160deg,#c7a894,#4b3a3a)}
.testimonial h4{position:absolute;left:320px;top:36px;font-family:var(--serif);font-weight:700;font-size:17px;color:var(--ink)}
.testimonial blockquote{position:absolute;left:320px;top:70px;width:790px;font-family:var(--serif);font-style:italic;font-size:15px;line-height:25px;color:#666}
.testimonial cite{position:absolute;left:320px;top:132px;font-family:var(--serif);font-style:italic;font-size:15px;color:var(--red)}
.t-dots{position:absolute;left:547px;top:178px;display:flex;gap:6px}
.t-dots span{width:30px;height:4px;background:#cfcfcf}
.t-dots span:first-child{background:var(--red)}

/* ratings */
.ratings h2{position:absolute;top:1958px;width:100%;text-align:center;font-family:var(--serif);font-size:24px;color:var(--black)}
.badge-round{position:absolute;border-radius:50%}

/* footer */
.footer{position:absolute;left:0;top:2163px;width:1200px;height:306px;background:var(--footer);border-top:5px solid var(--red);color:#cfcfcf}
.f-brand{position:absolute;left:85px;top:78px;width:270px;text-align:center;font-family:var(--serif);color:var(--white)}
.f-brand .name{font-size:42px;line-height:48px}
.f-brand .pc{display:flex;align-items:center;gap:12px;font-size:18px}
.f-brand .pc::before,.f-brand .pc::after{content:"";flex:1;height:2px;background:var(--white)}
.f-col{position:absolute;top:34px}
.f-col h5{font-family:var(--serif);font-size:17px;font-weight:700;color:var(--white);margin-bottom:22px}
.f-links{list-style:none;font-size:12.5px;line-height:23px}
.divider{position:absolute;top:34px;width:1px;height:205px;background:var(--footer-line)}
.f-col p{font-size:12.5px;line-height:21px}
.email-field{margin-top:14px;width:231px;height:34px;background:var(--white);color:#888;font-size:12px;padding:9px 12px}
.subscribe{margin-top:12px;width:101px;height:36px;border:2px solid var(--white);color:var(--white);font-size:12px;font-weight:700;display:flex;align-items:center;justify-content:center}
.c-row{display:flex;gap:22px;font-size:12.5px;line-height:19px;margin-bottom:12px}
.c-row svg{flex:none;margin-top:2px}
.copyright{position:absolute;left:99px;top:258px;font-size:12px;color:#ccc}
.f-social{position:absolute;left:986px;top:246px;display:flex;gap:10px}
.f-social span{width:36px;height:36px;border-radius:50%;border:2px solid var(--white)}
</style>
</head>
<body>

<div class="topline"></div>

<header>
  <a class="brand" href="#"><div class="name">Marigold Law</div><div class="pc">P.C</div></a>
  <div class="social-top"><span class="dot blue"></span><span class="dot sky"></span><span class="dot teal"></span></div>
  <div class="contact-top" style="left:690px">
    <span class="ring"><svg width="13" height="13" viewBox="0 0 24 24"><path fill="#ec1f27" d="M6.6 10.8a15 15 0 0 0 6.6 6.6l2.2-2.2c.3-.3.7-.4 1-.2 1.1.4 2.3.6 3.6.6.6 0 1 .4 1 1V20c0 .6-.4 1-1 1A17 17 0 0 1 3 4c0-.6.4-1 1-1h3.5c.6 0 1 .4 1 1 0 1.3.2 2.5.6 3.6.1.3 0 .7-.2 1z"/></svg></span>
    (555) 014-2290
  </div>
  <div class="contact-top" style="left:842px">
    <span class="ring"><svg width="13" height="11" viewBox="0 0 24 18"><path fill="#ec1f27" d="M0 0h24v18H0z"/><path fill="#fff" d="M1.5 1.5 12 10l10.5-8.5" stroke="#fff" stroke-width="2"/></svg></span>
    renata@marigoldlawgroup.com
  </div>
  <nav class="nav">
    <a class="active" href="#">Home</a><a href="#">Attorney Profile</a><a href="#">Practice Areas</a><a href="#">Client Reviews</a><a href="#">Links</a><a href="#">Contact Us</a>
    <svg width="15" height="15" viewBox="0 0 24 24"><circle cx="10" cy="10" r="7" fill="none" stroke="#1c1c1c" stroke-width="3"/><path d="M15 15l7 7" stroke="#1c1c1c" stroke-width="3"/></svg>
  </nav>
</header>

<section class="hero" role="img" aria-label="City skyline with high-rise towers">
  <h1>Marigold Law, P.C.</h1>
  <p>Marigold Law P.C. is owned by Renata L. Marigold, a dedicated and caring professional</p>
  <a class="btn-red" href="#">GET MORE INFO &gt;&gt;</a>
  <div class="slider-dots"><span></span><span></span><span></span></div>
</section>

<section class="welcome">
  <h2>WELCOME TO MARIGOLD LAW P.C.</h2>
  <p style="top:617px">Marigold Law P.C. is owned by Renata L. Marigold, a dedicated and caring professional who uses her broad range of skills as a California lawyer to bring consumers and business owners exceptionally strong legal representation that achieves best results. She works with people from across the northern region of California, from the Northern border to the Central Valley region.</p>
  <p style="top:722px">They bring her legal concerns and problems that occur in many areas of law, including Real Estate, Family law, Business Law, Bankruptcy, Criminal Law and Civil Litigation.</p>
  <a class="read-more" style="left:99px;top:796px" href="#">READ MORE &gt;&gt;</a>
  <div class="wordcloud" role="img" aria-label="Word cloud of legal terms around criminal law, justice and legal"></div>
</section>

<section class="band" aria-label="Practice areas">
  <span class="v" style="left:149px;top:0;height:66px"></span><span class="pin" style="left:144px;top:64px"></span>
  <span class="v" style="left:442px;top:0;height:66px"></span><span class="pin" style="left:437px;top:64px"></span>
  <span class="v" style="left:735px;top:0;height:66px"></span><span class="pin" style="left:730px;top:64px"></span>
  <span class="v" style="left:1028px;top:0;height:66px"></span><span class="pin" style="left:1023px;top:64px"></span>
  <span class="pin" style="left:290px;top:201px"></span><span class="v" style="left:295px;top:206px;height:78px"></span>
  <span class="pin" style="left:583px;top:201px"></span><span class="v" style="left:588px;top:206px;height:78px"></span>
  <span class="pin" style="left:876px;top:201px"></span><span class="v" style="left:881px;top:206px;height:78px"></span>

  <div class="area" style="left:70px;top:120px">
    <svg width="92" height="42" viewBox="0 0 92 42"><rect x="0" y="8" width="16" height="26" fill="#fff"/><rect x="76" y="8" width="16" height="26" fill="#fff"/><path d="M18 14h20l10 6 10-6h16v18l-14 8-22 0-20-10z" fill="#fff"/></svg>
    Business Law</div>
  <div class="area" style="left:218px;top:60px">
    <svg width="70" height="52" viewBox="0 0 70 52"><rect x="2" y="18" width="16" height="34" fill="#fff"/><rect x="22" y="2" width="22" height="50" fill="#fff"/><rect x="48" y="12" width="18" height="40" fill="#fff"/><g fill="#d8232a"><rect x="26" y="8" width="4" height="4"/><rect x="36" y="8" width="4" height="4"/><rect x="26" y="18" width="4" height="4"/><rect x="36" y="18" width="4" height="4"/><rect x="26" y="28" width="4" height="4"/><rect x="36" y="28" width="4" height="4"/></g></svg>
    Real Estate Law</div>
  <div class="area" style="left:363px;top:108px">
    <svg width="60" height="54" viewBox="0 0 60 54"><path d="M4 2v48h54" fill="none" stroke="#fff" stroke-width="3"/><rect x="12" y="20" width="8" height="28" fill="#fff"/><rect x="24" y="28" width="8" height="20" fill="#fff"/><rect x="36" y="36" width="8" height="12" fill="#fff"/><path d="M10 8l36 24" stroke="#fff" stroke-width="3"/></svg>
    Bankruptcy</div>
  <div class="area" style="left:510px;top:60px">
    <svg width="60" height="52" viewBox="0 0 60 52"><circle cx="18" cy="26" r="13" fill="none" stroke="#fff" stroke-width="6"/><circle cx="42" cy="34" r="13" fill="none" stroke="#fff" stroke-width="6"/><path d="M26 14l10 8" stroke="#fff" stroke-width="5"/></svg>
    Criminal Law</div>
  <div class="area" style="left:656px;top:108px">
    <svg width="64" height="54" viewBox="0 0 64 54"><path d="M32 0 64 14H0z" fill="#fff"/><g fill="#fff"><rect x="6" y="18" width="8" height="26"/><rect x="20" y="18" width="8" height="26"/><rect x="36" y="18" width="8" height="26"/><rect x="50" y="18" width="8" height="26"/><rect x="0" y="46" width="64" height="8"/></g></svg>
    Civil Litigation</div>
  <div class="area" style="left:803px;top:52px">
    <svg width="72" height="62" viewBox="0 0 72 62"><g fill="#fff"><circle cx="14" cy="7" r="6"/><rect x="6" y="16" width="16" height="44"/><circle cx="58" cy="7" r="6"/><path d="M50 16h16l4 28h-24z"/><rect x="52" y="44" width="12" height="16"/><circle cx="36" cy="26" r="5"/><rect x="30" y="34" width="12" height="26"/></g></svg>
    Family Law</div>
  <div class="area" style="left:950px;top:108px">
    <svg width="56" height="56" viewBox="0 0 56 56"><circle cx="28" cy="28" r="23" fill="none" stroke="#fff" stroke-width="7"/><path d="M12 44 44 12" stroke="#fff" stroke-width="7"/></svg>
    Unlawful Detainer</div>
</section>

<section class="blog">
  <h2 class="blog-title">OUR BLOG</h2>
  <a class="arrow-btn" style="left:55px" href="#"><svg width="10" height="16" viewBox="0 0 10 16"><path d="M8 2 2 8l6 6" fill="none" stroke="#aaa" stroke-width="2"/></svg></a>
  <a class="arrow-btn" style="left:1103px" href="#"><svg width="10" height="16" viewBox="0 0 10 16"><path d="M2 2l6 6-6 6" fill="none" stroke="#aaa" stroke-width="2"/></svg></a>

  <article class="card" style="left:99px">
    <div class="photo" role="img" aria-label="Business meeting around a glass conference table" style="background:linear-gradient(160deg,#3a3d44,#1a1b1f 60%,#6a6f78)"></div>
    <h3>At vero eos et accusamus et iust</h3>
    <div class="meta"><span>&#9635; 25/02/2016</span><i>|</i><span>&#9679; John Doe</span></div>
    <p>Nam libero tempore, cum soluta nobis est eligendi optio cumque nihil impedit quo minus id quod maxime place at facere possimu omnis volu.</p>
    <a class="more" href="#">READ MORE &gt;&gt;</a>
  </article>
  <article class="card" style="left:441px">
    <div class="photo" role="img" aria-label="Rental agreement document with keys and a pen" style="background:linear-gradient(160deg,#c9ccd0,#eef0f2 50%,#8a9097)"></div>
    <h3>At vero eos et accusamus et iust</h3>
    <div class="meta"><span>&#9635; 25/02/2016</span><i>|</i><span>&#9679; John Doe</span></div>
    <p>Nam libero tempore, cum soluta nobis est eligendi optio cumque nihil impedit quo minus id quod maxime place at facere possimu omnis volu.</p>
    <a class="more" href="#">READ MORE &gt;&gt;</a>
  </article>
  <article class="card" style="left:785px">
    <div class="photo" role="img" aria-label="Couple shaking hands with an advisor" style="background:linear-gradient(160deg,#b4bcc4,#d9c7a8 50%,#6d6660)"></div>
    <h3>At vero eos et accusamus et iust</h3>
    <div class="meta"><span>&#9635; 25/02/2016</span><i>|</i><span>&#9679; John Doe</span></div>
    <p>Nam libero tempore, cum soluta nobis est eligendi optio cumque nihil impedit quo minus id quod maxime place at facere possimu omnis volu.</p>
    <a class="more" href="#">READ MORE &gt;&gt;</a>
  </article>
</section>

<section class="testimonial">
  <div class="quote-bg"></div>
  <div class="avatar" role="img" aria-label="Portrait of the reviewer"></div>
  <h4>A Vital Component</h4>
  <blockquote>Marigold Law is our go-to source for professional and sound legal advice. Marigold Law has become a vital component to the success of our business as well as the businesses of the clients we have referred to Marigold Law.</blockquote>
  <cite>- Ridgeline Accounting Partners</cite>
  <div class="t-dots"><span></span><span></span><span></span></div>
</section>

<section class="ratings">
  <h2>RATINGS AND REVIEWS</h2>
  <div class="badge-round" style="left:288px;top:2011px;width:100px;height:100px;background:#eef1f5;border:3px solid #23427a"></div>
  <div class="badge-round" style="left:503px;top:2010px;width:100px;height:100px;background:#f4f4f4;border:3px solid #222"></div>
  <div class="abs" style="left:724px;top:2040px;width:192px;height:34px;background:#d7e2ee"></div>
</section>

<footer class="footer">
  <div class="f-brand"><div class="name">Marigold Law</div><div class="pc">P.C</div></div>
  <span class="divider" style="left:404px"></span>
  <span class="divider" style="left:574px"></span>
  <span class="divider" style="left:866px"></span>

  <div class="f-col" style="left:428px">
    <h5>Information</h5>
    <ul class="f-links"><li>Home</li><li>Attorney Profile</li><li>Practice Areas</li><li>Client Reviews</li><li>Links</li><li>Contact Us</li></ul>
  </div>
  <div class="f-col" style="left:598px">
    <h5>Newsletter</h5>
    <p>Register your email address to get<br>information ablout us</p>
    <div class="email-field">Email Address</div>
    <div class="subscribe">SUBSCRIBE</div>
  </div>
  <div class="f-col" style="left:892px">
    <h5>Contact Us</h5>
    <div class="c-row"><svg width="10" height="14" viewBox="0 0 10 14"><path d="M5 0a5 5 0 0 0-5 5c0 4 5 9 5 9s5-5 5-9a5 5 0 0 0-5-5z" fill="#fff"/><circle cx="5" cy="5" r="2" fill="#1e1e1e"/></svg><span>48 Orchard Lane, Suite 310<br>Fairview, CA 95000</span></div>
    <div class="c-row"><svg width="12" height="12" viewBox="0 0 24 24"><path fill="#fff" d="M6.6 10.8a15 15 0 0 0 6.6 6.6l2.2-2.2c.3-.3.7-.4 1-.2 1.1.4 2.3.6 3.6.6.6 0 1 .4 1 1V20c0 .6-.4 1-1 1A17 17 0 0 1 3 4c0-.6.4-1 1-1h3.5c.6 0 1 .4 1 1 0 1.3.2 2.5.6 3.6.1.3 0 .7-.2 1z"/></svg><span>(555) 014-2290</span></div>
    <div class="c-row"><svg width="13" height="12" viewBox="0 0 13 12"><rect x="0" y="3" width="13" height="9" fill="#fff"/><rect x="3" y="0" width="7" height="4" fill="#fff"/></svg><span>(555) 017-8841</span></div>
    <div class="c-row"><svg width="13" height="10" viewBox="0 0 24 18"><path fill="#fff" d="M0 0h24v18H0z"/><path d="M1.5 1.5 12 10l10.5-8.5" fill="none" stroke="#1e1e1e" stroke-width="2"/></svg><span>renata@marigoldlawgroup.com</span></div>
  </div>

  <div class="copyright">Copyrights © 2016 ,Marigold Law P.C. All rights reserved.</div>
  <div class="f-social"><span></span><span></span><span></span></div>
</footer>

</body>
</html>
```